indépendant en tant que Massothérapeute et Préparateur Mental, j'ai besoin de ...

Massothérapeute et préparateur mental indépendant, je recherche une carte de visite sobre et dynamique, sans images liées au massage ou à la préparation mentale mais intégrant mon logo. Les couleurs que j'aime bien sont : Blanc, gris, anthracite, noir et jaune

Contact Information for Business Card

carte de préférence Horizontale
neutre qui puisse toucher le deux domaines Massothérapie et préparation mentale

Requirements
Must have
• mon projet doit intégrer au recto:
LOGO
Loïc Bardèze
078 513 26 48
info@loicbardeze.ch
et éventuellement www.loicbardeze.ch

et au verso les deux adresses:

Chemin des Ormilles 7B
1400 Yverdon-les-Bains

Route de la Gravière 9
1700 Fribourg

Should not have
• mon projet ne doit pas contenir d'image en liens avec le massage ni la préparation mentale.

```html
<!DOCTYPE html>
<html lang="fr">
<head>
<meta charset="utf-8">
<title>Loïc Bardèze – Carte de visite</title>
<link rel="stylesheet" href="https://fonts.googleapis.com/css2?family=Lato:wght@400;700;900&display=swap">
<style>
  :root {
    --backdrop: #dcdcde;
    --card: #ebebee;
    --yellow: #e8e56a;
    --ink: #111111;
    --rule: #c9c64f;
  }
  * { margin: 0; padding: 0; box-sizing: border-box; }
  html, body {
    width: 1200px; height: 801px; overflow: hidden;
    background: var(--backdrop);
    font-family: "Lato", Arial, sans-serif;
    color: var(--ink);
  }
  .stage { position: relative; width: 1200px; height: 801px; }

  .card {
    position: absolute;
    width: 514px; height: 310px;
    background: var(--card);
  }
  .card--back { left: 355px; top: 46px; }
  .card--front { left: 354px; top: 423px; }

  /* Verso : adresses */
  .address-panel {
    position: absolute; left: 22px; top: 21px;
    width: 470px; height: 266px;
    background: var(--yellow);
  }
  .wordmark {
    position: absolute;
    display: flex; align-items: center; gap: 6px;
    font-weight: 900; white-space: nowrap;
  }
  .wordmark__square { width: 9px; height: 9px; background: var(--ink); }
  .address-panel .wordmark { right: 270px; top: 125px; font-size: 13px; }

  .addresses { position: absolute; left: 210px; top: 78px; width: 180px; }
  .addresses__title {
    font-size: 13px; font-weight: 700; letter-spacing: 0.14em;
    padding: 0 0 3px 2px;
    border-bottom: 1px solid var(--rule);
  }
  .address { font-size: 11.5px; line-height: 15.5px; }
  .address:first-of-type { margin-top: 10px; }
  .address-divider { width: 14px; border: 0; border-top: 1px solid var(--ink); margin: 7px 0 6px; }

  /* Recto : contact */
  .holder-name {
    position: absolute; left: 33px; top: 172px;
    font-size: 18.5px; font-weight: 700; letter-spacing: 0.03em;
  }
  .contact { position: absolute; left: 35px; top: 211px; list-style: none; font-size: 13px; }
  .contact li { height: 22px; line-height: 18px; letter-spacing: 0.02em; }
  .contact b { font-weight: 700; display: inline-block; width: 18px; }
  .card--front .wordmark { left: 276px; top: 246px; font-size: 19px; gap: 8px; }
  .card--front .wordmark__square { width: 14px; height: 14px; }
</style>
</head>
<body>
<main class="stage">

  <section class="card card--back" aria-label="Verso de la carte">
    <div class="address-panel">
      <div class="wordmark"><span class="wordmark__square"></span>Loïc Bardèze</div>
      <div class="addresses">
        <h2 class="addresses__title">ADRESSES</h2>
        <p class="address">Chemin des Ormilles 7B<br>1400 Yverdon-les-Bains</p>
        <hr class="address-divider">
        <p class="address">Route de la Gravière 9<br>1700 Fribourg</p>
      </div>
    </div>
  </section>

  <section class="card card--front" aria-label="Recto de la carte">
    <h1 class="holder-name">LOÏC BARDÈZE</h1>
    <ul class="contact">
      <li><b>M</b>: 078 513 26 48</li>
      <li><b>E</b>: info@loicbardeze.ch</li>
      <li><b>W</b>: www.loicbardeze.ch</li>
    </ul>
    <div class="wordmark"><span class="wordmark__square"></span>Loïc Bardèze</div>
  </section>

</main>
</body>
</html>
```